Business card - mobile service

O KiraLink is a mobile family safety service based on tablets and smartphones.
The business card must have:
BASIC INFO
Company Logo
Name
Position / Job Title: Co-founder
Mobile Phone Number: +55 (11) 5080 6192
Land Line: +55 (11) 8765 093412
Email Address: name@kiralink-example.com
Web Site URL: www.kiralink-example.com
PROMOTIONAL INFO
Try KiraLink free Today!
Your personal promo code: qqqq-5151-hhhh-3030-9876
Promo code text explanation with the instructions about the trial offer
Updates
Dears,
One more must have: the KiraLink slogan:
Industry/Entity Type
Safety
Look and feel
Each slider illustrates characteristics of the customer's brand and the style your logo design should communicate.

```html
<!DOCTYPE html>
<html lang="en">
<head>
<meta charset="utf-8">
<title>KiraLink business card</title>
<link rel="stylesheet" href="https://fonts.googleapis.com/css2?family=Arimo:wght@400;700&family=Tinos&display=swap">
<style>
  :root {
    --backdrop: #d9d9d9;
    --orange-deep: #e8650a;
    --orange-mid: #f39a12;
    --orange-light: #f7b52a;
    --brand-blue: #1aa6e6;
    --white: #ffffff;
    --ink: #2b2b2b;
    --accent: #e8770f;
  }
  * { margin: 0; padding: 0; box-sizing: border-box; }
  html, body { width: 1200px; height: 944px; overflow: hidden; }
  body { background: var(--backdrop); position: relative; font-family: "Arimo", sans-serif; }

  .card {
    position: absolute;
    width: 620px;
    height: 354px;
    box-shadow: 0 10px 28px rgba(0,0,0,0.28);
    overflow: hidden;
  }

  /* Front */
  .card--front {
    left: 110px;
    top: 90px;
    background: radial-gradient(ellipse at 60% 40%, var(--orange-light) 0%, var(--orange-mid) 45%, var(--orange-deep) 100%);
  }
  .brand {
    position: absolute;
    display: flex;
    align-items: center;
    gap: 14px;
  }
  .brand__dot {
    border-radius: 50%;
    background: var(--white);
  }
  .brand__name {
    font-family: "Arimo", sans-serif;
    font-weight: 700;
    color: var(--brand-blue);
    letter-spacing: -1px;
    line-height: 1;
  }
  .card--front .brand { left: 0; right: 0; top: 90px; justify-content: center; }
  .card--front .brand__name { font-size: 76px; }
  .card--front .brand__dot { width: 40px; height: 40px; }
  .promo-line {
    position: absolute;
    left: 0; right: 0;
    top: 222px;
    text-align: center;
    font-family: "Tinos", serif;
    font-size: 21px;
    color: var(--white);
    text-transform: uppercase;
    letter-spacing: 0.5px;
  }
  .promo-code {
    position: absolute;
    left: 0; right: 0;
    top: 262px;
    text-align: center;
    font-size: 15px;
    color: var(--white);
  }
  .promo-code__value { font-weight: 700; letter-spacing: 0.5px; }
  .promo-note {
    position: absolute;
    left: 0; right: 0;
    top: 290px;
    text-align: center;
    font-size: 13px;
    color: var(--white);
  }

  /* Back */
  .card--back {
    left: 470px;
    top: 500px;
    background: var(--white);
  }
  .card__band { position: absolute; inset: 0; width: 620px; height: 354px; }
  .contact {
    position: absolute;
    left: 34px;
    top: 60px;
    color: var(--ink);
  }
  .contact__name {
    font-size: 22px;
    color: var(--accent);
    text-transform: uppercase;
    letter-spacing: 0.5px;
  }
  .contact__role { font-size: 17px; margin-top: 2px; }
  .contact__list { list-style: none; margin-top: 38px; font-size: 14px; line-height: 1.45; }
  .contact__label { color: var(--accent); display: inline-block; width: 18px; }
  .contact__web { color: var(--accent); }
  .card--back .brand { left: 340px; top: 140px; }
  .card--back .brand__name { font-size: 50px; }
  .card--back .brand__dot { width: 26px; height: 26px; }
  .slogan {
    position: absolute;
    left: 320px;
    right: 20px;
    top: 226px;
    text-align: center;
    font-family: "Tinos", serif;
    font-size: 18px;
    color: var(--white);
  }
</style>
</head>
<body>
  <section class="card card--front" aria-label="Business card front">
    <div class="brand">
      <span class="brand__name">KiraLink</span>
      <span class="brand__dot"></span>
    </div>
    <p class="promo-line">Try KiraLink free Today!</p>
    <p class="promo-code">Your personal promo code: <span class="promo-code__value">qqqq-5151-hhhh-3030-9876</span></p>
    <p class="promo-note">Enter this code at sign-up for 30 days of free premium access.</p>
  </section>

  <section class="card card--back" aria-label="Business card back">
    <svg class="card__band" viewBox="0 0 620 354" aria-hidden="true">
      <defs>
        <radialGradient id="bandGradient" cx="0.65" cy="0.45" r="0.7">
          <stop offset="0" stop-color="#f7b52a"/>
          <stop offset="0.5" stop-color="#f39a12"/>
          <stop offset="1" stop-color="#e8650a"/>
        </radialGradient>
      </defs>
      <path d="M335 0 Q255 170 290 354 L620 354 L620 0 Z" fill="url(#bandGradient)"/>
    </svg>
    <div class="contact">
      <h1 class="contact__name">Dario Menzel</h1>
      <p class="contact__role">Co-founder</p>
      <ul class="contact__list">
        <li><span class="contact__label">c:</span>+55 (11) 5080 6192</li>
        <li><span class="contact__label">p:</span>+55 (11) 8765 093412</li>
        <li><span class="contact__label">e:</span>dario@kiralink-example.com</li>
        <li class="contact__web">www.kiralink-example.com</li>
      </ul>
    </div>
    <div class="brand">
      <span class="brand__name">KiraLink</span>
      <span class="brand__dot"></span>
    </div>
    <p class="slogan">Your Family Safety Service</p>
  </section>
</body>
</html>
```